Bramblewood Card Company Business Cards

We are a trading card store with Glimmorax, sports and other TCG cards, we need a business card design that encompasses a clean cut, modern style with a retro flare. website is bramblewoodcardco.com for reference. Can utilize a comic book era feel or a more modern outdoor feel to utilize the "Pacific Northwest" elements of tress, mountains, etc.

Industry/Entity Type

Trading cards and collectibles

Contact Information for Business Card

business name, email address, phone number, name, owner job title

Font styles to use
Sans Serif

```html
<!DOCTYPE html>
<html lang="en">
<head>
<meta charset="utf-8">
<title>Bramblewood Card Company – Business Cards</title>
<link rel="stylesheet" href="https://fonts.googleapis.com/css2?family=Montserrat:wght@700&family=Open+Sans:wght@400&display=swap">
<style>
  :root {
    --backdrop: #2e2f31;
    --paper: #ffffff;
    --teal: #21bddd;
    --slate: #727272;
    --maroon: #74253b;
    --ink: #1e1e1e;
  }
  * { margin: 0; padding: 0; box-sizing: border-box; }
  html, body { width: 1200px; height: 1059px; overflow: hidden; }
  body {
    position: relative;
    background: var(--backdrop);
    font-family: "Open Sans", sans-serif;
    color: var(--ink);
  }
  .card {
    position: absolute;
    border-radius: 18px;
    overflow: hidden;
  }
  .card--front {
    left: 256px; top: 100px; width: 688px; height: 391px;
    background: var(--paper);
  }
  .card--back {
    left: 253px; top: 537px; width: 694px; height: 394px;
    background: var(--teal);
    display: flex; align-items: center; justify-content: center;
  }
  .brand-name {
    font-family: "Montserrat", sans-serif;
    font-weight: 700;
    color: var(--slate);
    text-align: center;
    text-transform: uppercase;
    line-height: 1.2;
  }
  .card--front .brand-name {
    position: absolute;
    left: 474px; top: 78px; width: 210px;
    font-size: 19px;
  }
  .card--back .brand-name {
    font-size: 40px;
    width: 400px;
  }
  .name-tab {
    position: absolute; left: 0; top: 194px;
    width: 14px; height: 39px;
    background: var(--teal);
    border-radius: 0 4px 4px 0;
  }
  .holder-name {
    position: absolute; left: 30px; top: 189px;
    font-family: "Montserrat", sans-serif;
    font-weight: 700;
    font-size: 34px;
    letter-spacing: 0.5px;
    color: var(--maroon);
    text-transform: uppercase;
    line-height: 1;
  }
  .holder-title {
    position: absolute; left: 31px; top: 220px;
    font-size: 16.5px;
    text-transform: uppercase;
    line-height: 1;
  }
  .rule {
    position: absolute; left: 134px; top: 229px;
    width: 524px; height: 2.5px;
    background: var(--teal);
  }
  .contact-list {
    position: absolute; left: 29px; top: 272px;
    list-style: none;
    font-size: 16.5px;
    line-height: 21px;
  }
  .contact-list li { display: flex; align-items: center; gap: 7px; }
  .contact-list svg { width: 11px; height: 11px; flex: none; }
  .address {
    position: absolute; right: 30px; top: 295px;
    font-size: 16.5px;
    line-height: 20px;
    text-align: right;
    font-style: normal;
  }
  .footer-wave {
    position: absolute; left: 0; bottom: 0;
    width: 688px; height: 40px;
  }
</style>
</head>
<body>
  <section class="card card--front" aria-label="Business card front">
    <p class="brand-name">Bramblewood<br>Card Company</p>

    <span class="name-tab"></span>
    <h1 class="holder-name">Dorian Vale</h1>
    <p class="holder-title">Manager</p>
    <span class="rule"></span>

    <ul class="contact-list">
      <li>
        <svg viewBox="0 0 12 12" aria-hidden="true"><path d="M2.5 1 L4.5 1 L5.2 3.6 L4 4.6 C4.6 6 6 7.4 7.4 8 L8.4 6.8 L11 7.5 L11 9.5 C11 10.3 10.3 11 9.5 11 C5 11 1 7 1 2.5 C1 1.7 1.7 1 2.5 1 Z" fill="var(--teal)"/></svg>
        555-0142-7788
      </li>
      <li>
        <svg viewBox="0 0 12 12" aria-hidden="true"><rect x="0.5" y="2" width="11" height="8" fill="var(--teal)"/><path d="M0.5 2 L6 6.5 L11.5 2 M0.5 10 L4.5 5.5 M11.5 10 L7.5 5.5" stroke="#fff" stroke-width="0.9" fill="none"/></svg>
        hello@bramblewoodcardco.com
      </li>
      <li>
        <svg viewBox="0 0 12 12" aria-hidden="true"><circle cx="6" cy="6" r="5.5" fill="var(--teal)"/><path d="M6 0.5 V11.5 M0.5 6 H11.5 M6 0.5 C3 3 3 9 6 11.5 M6 0.5 C9 3 9 9 6 11.5" stroke="#fff" stroke-width="0.7" fill="none"/></svg>
        www.bramblewoodcardco.com
      </li>
    </ul>

    <address class="address">
      2280 Alder Ridge Road South<br>
      Cedarvale, OR 97458 USA
    </address>

    <svg class="footer-wave" viewBox="0 0 688 40" preserveAspectRatio="none" aria-hidden="true">
      <path d="M0 14 L365 14 C362 18 355 21 345 21 L0 21 Z" fill="var(--slate)"/>
      <path d="M0 28 L335 28 C372 28 380 8 414 8 L688 8 L688 40 L0 40 Z" fill="var(--teal)"/>
    </svg>
  </section>

  <section class="card card--back" aria-label="Business card back">
    <p class="brand-name">Bramblewood<br>Card Company</p>
  </section>
</body>
</html>
```